Vantro cards

I am in the auto motive, transportation business I would like a business card that is Something cool, modern edgy, having to do with car culture. I offer towing service for high and exotic cars. I also provide towing for collisions and car accidents. I offer open and enclosed transport nationwide.

Target Market(s)

Car culture people high end auto collectors

Industry/Entity Type

Towing car carrier

Contact Information for Business Card

My company colors black yellow and silver

Font styles to use
Serif

```html
<!DOCTYPE html>
<html lang="en">
<head>
<meta charset="utf-8">
<title>Vantro Business Cards</title>
<link rel="stylesheet" href="https://fonts.googleapis.com/css2?family=Poppins:wght@400;500;700&display=swap">
<style>
  :root {
    --backdrop: #2a2a2a;
    --card: #0b0b0b;
    --yellow: #f5d44a;
    --silver: #c9c9c9;
    --ghost: #1c1c1c;
  }
  * { margin: 0; padding: 0; box-sizing: border-box; }
  html, body { width: 1200px; height: 1015px; overflow: hidden; }
  body {
    background: var(--backdrop);
    font-family: "Poppins", sans-serif;
    position: relative;
  }
  .card {
    position: absolute;
    width: 600px;
    height: 343px;
    background: var(--card);
    box-shadow: 0 14px 30px rgba(0,0,0,.55);
  }
  .card-front { left: 90px; top: 110px; }
  .card-back { left: 510px; top: 560px; }

  .brand {
    position: absolute;
    left: 0; right: 0; top: 110px;
    display: flex; align-items: center; justify-content: center; gap: 16px;
  }
  .brand-dot {
    width: 30px; height: 30px; border-radius: 50%;
    background: var(--yellow);
  }
  .brand-name {
    font-weight: 700; font-size: 62px; letter-spacing: 3px;
    color: var(--yellow); line-height: 1;
  }
  .front-web {
    position: absolute; left: 0; right: 0; bottom: 58px;
    text-align: center; color: var(--yellow);
    font-size: 17px; letter-spacing: 2px;
  }

  .ghost-mark {
    position: absolute; right: 26px; bottom: 40px;
    font-weight: 700; font-size: 92px; letter-spacing: 4px;
    color: var(--ghost); line-height: 1;
  }
  .person { position: absolute; left: 62px; top: 150px; }
  .person-name {
    font-weight: 700; font-size: 21px; color: var(--yellow);
    letter-spacing: .5px; line-height: 1.1;
  }
  .person-title {
    font-size: 13px; color: var(--silver); letter-spacing: 1px;
    margin-bottom: 24px;
  }
  .address { font-size: 17px; color: var(--silver); line-height: 1.35; }

  .contact { position: absolute; left: 330px; top: 48px; list-style: none; }
  .contact li {
    display: flex; align-items: center; gap: 8px;
    font-size: 16px; color: var(--silver); line-height: 1.5;
  }
  .contact svg { width: 15px; height: 15px; flex: none; }
</style>
</head>
<body>
  <section class="card card-front">
    <div class="brand">
      <span class="brand-dot"></span>
      <span class="brand-name">VANTRO</span>
    </div>
    <p class="front-web">www.vantrotow.com</p>
  </section>

  <section class="card card-back">
    <span class="ghost-mark" aria-hidden="true">VANTRO</span>

    <ul class="contact">
      <li>
        <svg viewBox="0 0 24 24" fill="var(--yellow)"><path d="M6.6 10.8a15 15 0 0 0 6.6 6.6l2.2-2.2c.3-.3.7-.4 1-.2 1.1.4 2.3.6 3.6.6.6 0 1 .4 1 1V20c0 .6-.4 1-1 1C10.6 21 3 13.4 3 4c0-.6.4-1 1-1h3.5c.6 0 1 .4 1 1 0 1.3.2 2.5.6 3.6.1.3 0 .7-.2 1z"/></svg>
        044-555 210 347
      </li>
      <li>
        <svg viewBox="0 0 24 24" fill="var(--yellow)"><path d="M2 5h20v14H2z M2 5l10 8 10-8" stroke="var(--card)" stroke-width="1.5"/></svg>
        info@vantrotow.com
      </li>
      <li>
        <svg viewBox="0 0 24 24" fill="none" stroke="var(--yellow)" stroke-width="2"><circle cx="12" cy="12" r="9"/><path d="M3 12h18M12 3c3 3 3 15 0 18M12 3c-3 3-3 15 0 18"/></svg>
        www.vantrotow.com
      </li>
    </ul>

    <div class="person">
      <h1 class="person-name">MARCUS HALE</h1>
      <p class="person-title">MANAGING DIRECTOR</p>
      <p class="address">421, Address line here<br>45452,Country Name</p>
    </div>
  </section>
</body>
</html>
```